Cool Website Design Gleam Shell Crew.

We need a new website, using our existing domain, with a similar function to https://www.marbeckfilm.com/ or https://www.tolvanfinishworks.com/ instagram gleam_shell.crew.
We can send google docs with pictures.
Logo attached

```html
<!DOCTYPE html>
<html lang="en">
<head>
<meta charset="utf-8">
<title>Gleam Shell Crew — Vehicle Wraps Calgary</title>
<link href="https://fonts.googleapis.com/css2?family=Bebas+Neue&family=Montserrat:wght@400;500;600;700&display=swap" rel="stylesheet">
<style>
:root{
  --black:#0b0b0c;
  --dark:#1c1c1e;
  --card:#222224;
  --purple:#6a1fd8;
  --blue:#2f6af5;
  --accent:#4b3cf0;
  --white:#ffffff;
  --muted:#c9c9cf;
  --grey:#8a8a90;
  --star:#f5a623;
  --grad:linear-gradient(90deg,#6a1fd8,#2f6af5);
}
*{margin:0;padding:0;box-sizing:border-box}
html,body{width:1200px;height:4412px;overflow:hidden;background:var(--dark)}
body{position:relative;font-family:'Montserrat',sans-serif;color:var(--white)}
.abs{position:absolute}
.heading{font-family:'Bebas Neue',sans-serif;font-weight:400;letter-spacing:.5px;line-height:1}
.underline{height:4px;width:68px;background:var(--grad)}
.btn{position:absolute;display:flex;align-items:center;justify-content:center;background:var(--grad);color:var(--white);font-weight:700;font-size:15px;clip-path:polygon(10px 0,100% 0,calc(100% - 10px) 100%,0 100%)}
.logo-name{font-family:'Montserrat',sans-serif;font-weight:700;color:#5b3df5;font-size:22px;line-height:1.1}
.ph{position:absolute}

/* header */
.header{left:0;top:0;width:1200px;height:120px;background:var(--black)}
.topbar{left:448px;top:0;width:752px;height:41px;background:var(--grad);clip-path:polygon(22px 0,100% 0,100% 100%,0 100%);display:flex;align-items:center;gap:34px;padding-left:46px;font-size:13px}
.topbar span{display:flex;align-items:center;gap:8px}
.nav{left:348px;top:72px;display:flex;gap:18px;font-size:12px;font-weight:500}
.nav .active{color:#7b4dff;text-decoration:underline}

/* hero */
.hero{left:0;top:120px;width:1200px;height:517px;background:#141414}
.hero-copy p{font-size:14px;line-height:26px;width:440px}

/* about */
.about{left:0;top:637px;width:1200px;height:715px;background:#1a1a1b}
.about-text{left:635px;top:818px;width:400px;font-size:14px;line-height:24px;color:var(--muted);text-align:justify;hyphens:auto;-webkit-hyphens:auto}
.stat{position:absolute;top:1180px;width:260px;text-align:center}
.stat b{display:block;font-size:46px;font-weight:600}
.stat span{font-size:19px;color:var(--muted)}

/* services */
.services{left:0;top:1352px;width:1200px;height:651px;background:var(--black)}
.card{position:absolute;top:1520px;width:310px;height:397px;background:var(--card);border-radius:8px;overflow:hidden;text-align:center}
.card .img{height:188px;margin:4px;border-radius:6px}
.card .icon{position:absolute;left:117px;top:158px;width:76px;height:76px;border-radius:50%;background:var(--grad);border:3px solid #fff;display:flex;align-items:center;justify-content:center}
.card h3{margin-top:60px;font-size:18px;font-weight:700}
.card p{margin:14px 22px 0;font-size:12.5px;line-height:24px;color:var(--muted)}
.card a{display:block;margin-top:12px;font-size:13px;font-weight:600;color:#7b4dff}
.arrow{position:absolute;width:38px;height:38px;border:2px solid #fff;border-radius:50%;display:flex;align-items:center;justify-content:center}

/* gallery */
.gallery-item{position:absolute;width:307px;height:246px}

/* testimonials */
.review{position:absolute;top:2977px;width:454px;height:319px;background:#fff;border-radius:4px;color:#333;padding:26px}
.review .stars{color:var(--star);font-size:18px;letter-spacing:2px}
.review p{margin-top:12px;font-size:13.5px;line-height:27px;color:#444}
.review .who{display:flex;align-items:center;gap:20px;margin-top:14px}
.review .avatar{width:88px;height:88px;border-radius:50%;background:linear-gradient(#c9ccd2,#8e96a3)}
.review b{font-size:16px;color:#222}
.review small{display:block;font-size:13px;color:#666;margin-top:8px}

/* contact */
.contact{left:0;top:3390px;width:600px;height:608px;background:linear-gradient(135deg,#6a1fd8,#2f6af5)}
.map{left:600px;top:3390px;width:600px;height:608px;background:linear-gradient(135deg,#e9ecef,#d8e6d2 60%,#cfe0ee)}
.c-item{position:absolute;left:120px;display:flex;gap:20px}
.c-item .ci{width:36px;height:36px;border-radius:50%;background:#111;display:flex;align-items:center;justify-content:center;flex:none}
.c-item h4{font-size:16px;font-weight:700}
.c-item p{font-size:13.5px;line-height:24px;margin-top:4px}

/* footer */
.footer{left:0;top:3998px;width:1200px;height:414px;background:var(--dark)}
.fcol h4{font-size:17px;font-weight:600;margin-bottom:16px}
.fcol li{list-style:none;font-size:15px;line-height:34px;color:#ddd}
.fcol li::before{content:"➔";font-size:12px;margin-right:10px}
</style>
</head>
<body>

<header class="abs header">
  <div class="abs" style="left:120px;top:28px;display:flex;align-items:center;gap:10px">
    <div style="width:30px;height:30px;background:#5b3df5"></div>
    <div class="logo-name">Gleam Shell<br>Crew</div>
  </div>
  <div class="abs topbar">
    <span><svg width="14" height="14" viewBox="0 0 24 24" fill="#fff"><path d="M6.6 10.8a15 15 0 006.6 6.6l2.2-2.2a1 1 0 011-.25 11 11 0 003.6.6 1 1 0 011 1V20a1 1 0 01-1 1A17 17 0 013 4a1 1 0 011-1h3.5a1 1 0 011 1 11 11 0 00.6 3.6 1 1 0 01-.25 1z"/></svg>+1 555 014 2290</span>
    <span><svg width="18" height="13" viewBox="0 0 24 18" fill="none" stroke="#fff" stroke-width="2"><rect x="1" y="1" width="22" height="16"/><path d="M1 1l11 9 11-9"/></svg>hello@gleamshellcrew.com</span>
    <span><svg width="14" height="18" viewBox="0 0 24 30" fill="#fff"><path d="M12 0a10 10 0 00-10 10c0 8 10 20 10 20s10-12 10-20A10 10 0 0012 0zm0 14a4 4 0 110-8 4 4 0 010 8z"/></svg>Calgary/Surrounding Areas</span>
  </div>
  <nav class="abs nav">
    <span class="active">HOME</span><span>|</span><span>ABOUT US</span><span>|</span><span>OUR SERVICES</span><span>|</span><span>WHY CHOOSE US</span><span>|</span><span>CONTACT US</span>
  </nav>
  <div class="btn" style="left:924px;top:60px;width:154px;height:43px">Get a Quote</div>
</header>

<section class="abs hero">
  <div class="ph" role="img" aria-label="Photo of a cream-wrapped sports sedan on a country road at dusk" style="left:608px;top:0;width:592px;height:517px;background:linear-gradient(160deg,#6d5346,#3d3a33 45%,#2a2a27)"></div>
  <div class="abs hero-copy" style="left:120px;top:84px">
    <div class="heading" style="font-size:40px">WELCOME TO</div>
    <div class="heading" style="font-size:84px;margin-top:8px">GLEAM SHELL CREW</div>
    <p style="margin-top:14px">Transform your vehicle with premium vinyl wraps, commercial graphics, and precision installation. Proudly serving Calgary with industry-leading quality, durability, and design.</p>
  </div>
  <div class="btn" style="left:123px;top:339px;width:223px;height:39px">Protect Your Vehicle</div>
</section>

<section class="abs about"></section>
<svg class="abs" style="left:90px;top:722px" width="470" height="378"><polygon points="58,2 452,2 402,376 2,376" fill="none" stroke="#4b3cf0" stroke-width="2"/></svg>
<div class="ph" role="img" aria-label="Photo of an installer squeegeeing blue vinyl wrap onto a car" style="left:166px;top:740px;width:215px;height:364px;background:linear-gradient(150deg,#a9c7e6,#1e6fd6 60%,#0f3f9a);clip-path:polygon(10% 0,100% 0,92% 100%,0 100%)"></div>
<div class="ph" role="img" aria-label="Photo of the front of a blue-wrapped car with a windshield banner" style="left:372px;top:740px;width:231px;height:364px;background:linear-gradient(170deg,#2a3d6a,#1b7bff 45%,#0b1f4a);clip-path:polygon(8% 0,100% 0,100% 100%,0 100%)"></div>
<div class="heading abs" style="left:635px;top:736px;font-size:38px">ABOUT US</div>
<div class="underline abs" style="left:635px;top:792px"></div>
<p class="abs about-text">Lorem Ipsum is simply dummy text of the printing and typesetting industry. Lorem Ipsum has been the industry's standard dummy text ever since the 1500s, when an unknown printer took a galley of type and scrambled it to make a type specimen book. It has survived not only five centuries, but also the leap into electronic typesetting, remaining essentially unchanged. It was popularised in the 1960s with the release of Presstype sheets containing Lorem Ipsum passages, and more recently</p>
<div class="btn" style="left:635px;top:1065px;width:158px;height:39px">Read More</div>
<div class="stat" style="left:79px"><b>500+</b><span>Vehicles Wrapped</span></div>
<div class="stat" style="left:336px"><b>50+</b><span>Commercial Fleets Service</span></div>
<div class="stat" style="left:623px"><b>10+</b><span>Transactions Completed</span></div>
<div class="stat" style="left:871px"><b>100%</b><span>Satisfaction Rate</span></div>

<section class="abs services"></section>
<div class="heading abs" style="left:0;width:1200px;text-align:center;top:1428px;font-size:40px">OUR SERVICES</div>
<div class="underline abs" style="left:566px;top:1482px"></div>
<div class="arrow" style="left:43px;top:1693px"><svg width="16" height="16" viewBox="0 0 16 16" fill="none" stroke="#fff" stroke-width="2"><path d="M14 8H2M7 3L2 8l5 5"/></svg></div>
<div class="arrow" style="left:1119px;top:1693px"><svg width="16" height="16" viewBox="0 0 16 16" fill="none" stroke="#fff" stroke-width="2"><path d="M2 8h12M9 3l5 5-5 5"/></svg></div>

<div class="card" style="left:116px">
  <div class="img" role="img" aria-label="Illustration of a race car with a blue and black wrap design" style="background:linear-gradient(160deg,#9aa0a8,#2a4fb0 55%,#111)"></div>
  <div class="icon"><svg width="34" height="28" viewBox="0 0 34 28" fill="none" stroke="#fff" stroke-width="2"><path d="M4 18l3-9h20l3 9v6H4z"/><circle cx="10" cy="20" r="2"/><circle cx="24" cy="20" r="2"/></svg></div>
  <h3>Full Vehicle Wraps</h3>
  <p>Upgrade your vehicle with a complete colour change or specialty finish. We offer matte, gloss, satin, metallic,</p>
  <a>Learn More &nbsp;›</a>
</div>
<div class="card" style="left:443px">
  <div class="img" role="img" aria-label="Illustration of a race car with a red and black fleet livery" style="background:linear-gradient(160deg,#9aa0a8,#b81e2a 55%,#111)"></div>
  <div class="icon"><svg width="30" height="30" viewBox="0 0 30 30" fill="none" stroke="#fff" stroke-width="2"><path d="M15 3l10 22H5z"/><circle cx="15" cy="17" r="3"/></svg></div>
  <h3>Fleet Graphics</h3>
  <p>Your fleet is your moving billboard. We provide consistent, durable branding for contractors, delivery vehicles, service</p>
  <a>Learn More &nbsp;›</a>
</div>
<div class="card" style="left:770px">
  <div class="img" role="img" aria-label="Illustration of pink and black decal swoosh graphics" style="background:linear-gradient(160deg,#f2f2f2,#e0338a 45%,#1a1a1a)"></div>
  <div class="icon"><svg width="34" height="22" viewBox="0 0 34 22" fill="none" stroke="#fff" stroke-width="2"><path d="M3 15c2-6 8-9 16-9 6 0 10 3 12 9z"/><circle cx="10" cy="16" r="2"/><circle cx="24" cy="16" r="2"/></svg></div>
  <h3>Decals &amp; Signage</h3>
  <p>Custom decals, spot graphics, window perf, storefront signs, and promotional materials. High-resolution prints, precise</p>
  <a>Learn More &nbsp;›</a>
</div>

<div class="heading abs" style="left:0;width:1200px;text-align:center;top:2120px;font-size:40px">OUR GALLERY</div>
<div class="underline abs" style="left:566px;top:2174px"></div>
<div class="gallery-item" role="img" aria-label="Photo of a white sedan rear view in snow" style="left:120px;top:2208px;background:linear-gradient(160deg,#dfe5ea,#9aa3ab)"></div>
<div class="gallery-item" role="img" aria-label="Photo of a red hatchback with black racing stripes" style="left:448px;top:2208px;background:linear-gradient(160deg,#8a8f93,#c7231c 50%,#3a3a3a)"></div>
<div class="gallery-item" role="img" aria-label="Photo of a white coupe with a dark roof decal" style="left:774px;top:2208px;background:linear-gradient(160deg,#7da0c8,#e8e8e8 55%,#5c6650)"></div>
<div class="gallery-item" role="img" aria-label="Photo of a green muscle car with a matte black hood" style="left:120px;top:2474px;background:linear-gradient(160deg,#8c8f92,#4f5a3a 55%,#1a1a1a)"></div>
<div class="gallery-item" role="img" aria-label="Photo of a lettered white service trailer" style="left:448px;top:2474px;background:linear-gradient(160deg,#f4f1ea,#cfc8b8)"></div>
<div class="gallery-item" role="img" aria-label="Photo of a black sedan with a bronze hood stripe" style="left:774px;top:2474px;background:linear-gradient(160deg,#5a6a72,#1c1f24 60%,#6b5033)"></div>
<div class="btn" style="left:522px;top:2768px;width:158px;height:41px">View More</div>

<div class="heading abs" style="left:0;width:1200px;text-align:center;top:2878px;font-size:40px">WHAT OUR CLIENTS SAY</div>
<div class="underline abs" style="left:566px;top:2932px"></div>
<div class="arrow" style="left:43px;top:3116px"><svg width="16" height="16" viewBox="0 0 16 16" fill="none" stroke="#fff" stroke-width="2"><path d="M14 8H2M7 3L2 8l5 5"/></svg></div>
<div class="arrow" style="left:1119px;top:3116px"><svg width="16" height="16" viewBox="0 0 16 16" fill="none" stroke="#fff" stroke-width="2"><path d="M2 8h12M9 3l5 5-5 5"/></svg></div>
<div class="review" style="left:135px">
  <div class="stars">★★★★★</div>
  <p>Lorem Ipsum is simply dummy text of the printing and typesetting industry. Lorem Ipsum has been the industry's standard dummy text ever since the 1500s, when an unknown printer took a galley of type and scrambled it to make a type specimen book.</p>
  <div class="who"><div class="avatar" role="img" aria-label="Client portrait"></div><div><b>Owen</b><small>Client</small></div></div>
</div>
<div class="review" style="left:613px">
  <div class="stars">★★★★★</div>
  <p>Lorem Ipsum is simply dummy text of the printing and typesetting industry. Lorem Ipsum has been the industry's standard dummy text ever since the 1500s, when an unknown printer took a galley of type and scrambled it to make a type specimen book.</p>
  <div class="who"><div class="avatar" role="img" aria-label="Client portrait"></div><div><b>Rafael</b><small>Client</small></div></div>
</div>

<section class="abs contact"></section>
<div class="abs map" role="img" aria-label="Street map of Calgary and surrounding neighbourhoods"></div>
<div class="heading abs" style="left:120px;top:3478px;font-size:40px">CONTACT US</div>
<div class="abs" style="left:120px;top:3534px;width:68px;height:4px;background:#fff"></div>
<div class="c-item" style="top:3576px"><div class="ci"><svg width="14" height="18" viewBox="0 0 24 30" fill="#fff"><path d="M12 0a10 10 0 00-10 10c0 8 10 20 10 20s10-12 10-20A10 10 0 0012 0zm0 14a4 4 0 110-8 4 4 0 010 8z"/></svg></div><div><h4>LOCATION WE SERVE</h4><p>Calgary/Surrounding Areas</p></div></div>
<div class="c-item" style="top:3648px"><div class="ci"><svg width="18" height="18" viewBox="0 0 20 20" fill="none" stroke="#fff" stroke-width="2"><circle cx="10" cy="10" r="8"/><path d="M10 5v5l3 2"/></svg></div><div><h4>WORKING HOURS</h4><p>Sunday: Closed<br>Monday To Friday: 9:00 AM – 9:00 PM<br>Saturday: 9:00 AM – 3:00 PM</p></div></div>
<div class="c-item" style="top:3772px"><div class="ci"><svg width="14" height="14" viewBox="0 0 24 24" fill="#fff"><path d="M6.6 10.8a15 15 0 006.6 6.6l2.2-2.2a1 1 0 011-.25 11 11 0 003.6.6 1 1 0 011 1V20a1 1 0 01-1 1A17 17 0 013 4a1 1 0 011-1h3.5a1 1 0 011 1 11 11 0 00.6 3.6 1 1 0 01-.25 1z"/></svg></div><div><h4>CALL US</h4><p>+1 555 014 2290</p></div></div>
<div class="c-item" style="top:3844px"><div class="ci"><svg width="16" height="12" viewBox="0 0 24 18" fill="none" stroke="#fff" stroke-width="2"><rect x="1" y="1" width="22" height="16"/><path d="M1 1l11 9 11-9"/></svg></div><div><h4>MAIL US</h4><p>hello@gleamshellcrew.com</p></div></div>

<footer class="abs footer"></footer>
<div class="abs" style="left:163px;top:4110px;display:flex;align-items:center;gap:10px">
  <div style="width:30px;height:30px;background:#5b3df5"></div>
  <div class="logo-name">Gleam Shell<br>Crew</div>
</div>
<div class="abs fcol" style="left:423px;top:4078px"><h4>MAIN LINKS</h4><ul><li>Home</li><li>About Us</li><li>Our Services</li><li>Gallery</li><li>Why choose us</li><li>Contact</li></ul></div>
<div class="abs fcol" style="left:628px;top:4078px"><h4>HELP LINKS</h4><ul><li>Privacy Policy</li><li>Support Links</li><li>Terms of Use</li></ul></div>
<div class="abs fcol" style="left:841px;top:4078px"><h4>NEWSLETTER SIGN UP</h4><p style="font-size:12px;line-height:22px;color:#ddd">We Will Notify You Of Any<br>Important News</p></div>
<div class="abs" style="left:837px;top:4182px;width:202px;height:40px;background:#fff;border-radius:4px;display:flex;align-items:center;padding-left:10px;font-size:12px;color:#333">Your Email Address</div>
<div class="abs" style="left:993px;top:4182px;width:46px;height:40px;background:var(--grad);border-radius:0 4px 4px 0;display:flex;align-items:center;justify-content:center"><svg width="20" height="20" viewBox="0 0 24 24" fill="none" stroke="#fff" stroke-width="2"><path d="M22 2L11 13M22 2l-7 20-4-9-9-4z"/></svg></div>
<div class="abs" style="left:120px;top:4362px;width:960px;height:1px;background:#555"></div>
<div class="abs" style="left:0;width:1200px;top:4382px;text-align:center;font-size:12px;color:#ccc">© 2025 Gleam Shell Crew | All Rights Reserved</div>

</body>
</html>
```